Building company buisness cards

We are looking for a sharp modern new look for our business cards.We are a New Zealand based company that specialises in house and land packages.We have attached a photo of the current logo and would like to see if it can be improved somehow if needed.We are open to any colours but we have chosen Black and White at this stage. Feel free to change the font and make the logo smarter looking.Play with the colours and see what looks best.We want a card that looks so good know one will want to throw it away!

Target Market(s)

Building profesonals, home buyers

Industry/Entity Type

Building

Contact Information for Business Card

Garrick Tenwood
0275390628
garrickt@hartvale.co.nz

Font styles to use
Serif
Sans Serif

Colors

Designer to choose colors to be used in the design.

Requirements
Must have
• Just the logo on one side and details on the other
• Clean simple looking card
Nice to have
• Round corners and detail like raised or spot UV
• Something that stands out
Should not have
• To title needed, Director etc

```html
<!DOCTYPE html>
<html lang="en">
<head>
<meta charset="utf-8">
<title>Hartvale – Business Cards</title>
<link rel="stylesheet" href="https://fonts.googleapis.com/css2?family=Bitter:wght@700&family=Oswald:wght@500&family=Quicksand:wght@500&display=swap">
<style>
  :root {
    --backdrop: #5e5e5e;
    --backdrop-light: #6c6c6c;
    --card: #151515;
    --spot-gloss: #2e2e2e;
    --spot-name: #0a0a0a;
    --detail: #8c8c8c;
    --divider: #3a3a3a;
  }
  * { margin: 0; padding: 0; box-sizing: border-box; }
  html, body {
    width: 1200px;
    height: 857px;
    overflow: hidden;
  }
  body {
    background: radial-gradient(ellipse at 40% 35%, var(--backdrop-light), var(--backdrop));
    position: relative;
  }
  .card {
    position: absolute;
    top: 280px;
    width: 520px;
    height: 297px;
    background: var(--card);
    border-radius: 10px;
  }
  .card--front { left: 60px; }
  .card--back { left: 620px; }

  /* Front: brand name only */
  .brand {
    position: absolute;
    inset: 0;
    display: flex;
    align-items: center;
    justify-content: center;
  }
  .brand__name {
    display: inline-flex;
    align-items: center;
    gap: 14px;
    font-family: "Bitter", serif;
    font-weight: 700;
    font-size: 44px;
    color: var(--spot-gloss);
    letter-spacing: 0.5px;
  }
  .brand__mark {
    width: 14px;
    height: 14px;
    background: var(--spot-gloss);
  }

  /* Back: name and contact details */
  .details {
    position: absolute;
    inset: 0;
    display: flex;
    align-items: center;
    justify-content: center;
    gap: 22px;
  }
  .details__name {
    font-family: "Oswald", sans-serif;
    font-weight: 500;
    font-size: 21px;
    letter-spacing: 0.5px;
    text-transform: uppercase;
    color: var(--spot-name);
  }
  .details__divider {
    width: 1px;
    height: 66px;
    background: var(--divider);
  }
  .contact-list {
    list-style: none;
    display: flex;
    flex-direction: column;
    gap: 7px;
  }
  .contact-list__item {
    display: flex;
    align-items: center;
    gap: 9px;
    font-family: "Quicksand", sans-serif;
    font-weight: 500;
    font-size: 13px;
    color: var(--detail);
  }
  .contact-list__icon {
    width: 12px;
    height: 12px;
    fill: var(--detail);
    flex: none;
  }
</style>
</head>
<body>
  <section class="card card--front" aria-label="Card front">
    <div class="brand">
      <div class="brand__name"><span>Hartvale</span><span class="brand__mark"></span></div>
    </div>
  </section>

  <section class="card card--back" aria-label="Card back">
    <div class="details">
      <h1 class="details__name">Garrick Tenwood</h1>
      <span class="details__divider"></span>
      <ul class="contact-list">
        <li class="contact-list__item">
          <svg class="contact-list__icon" viewBox="0 0 24 24" aria-hidden="true"><path d="M6.6 10.8a15.1 15.1 0 0 0 6.6 6.6l2.2-2.2a1 1 0 0 1 1-.25 11.4 11.4 0 0 0 3.6.57 1 1 0 0 1 1 1V20a1 1 0 0 1-1 1A17 17 0 0 1 3 4a1 1 0 0 1 1-1h3.5a1 1 0 0 1 1 1c0 1.250.2 2.450.57 3.570a1 1 0 0 1-.25 1z"/></svg>
          <span>0275390628</span>
        </li>
        <li class="contact-list__item">
          <svg class="contact-list__icon" viewBox="0 0 24 24" aria-hidden="true"><path d="M2 5h20v14H2zm2 2v.5l8 5 8-5V7zm0 2.9V17h16V9.9l-8 5z"/></svg>
          <span>garrickt@hartvale.co.nz</span>
        </li>
        <li class="contact-list__item">
          <svg class="contact-list__icon" viewBox="0 0 24 24" aria-hidden="true"><circle cx="12" cy="12" r="10"/></svg>
          <span>www.hartvale.co.nz</span>
        </li>
      </ul>
    </div>
  </section>
</body>
</html>
```